Flat bootstrap design for existing site

I'm looking for a modern flat design based around an existing logo. This has to be a custom design (no external templates), and implemented into a bootstrap framework.

The logo is attached as 2 versions - choose whichever you want, that flows better with whatever design you choose.

Added screenshots of the existing site (currently using the default bootstrap layouts). Please make your designs around those pages in the screenshots (i.e. the homepage only has the postal code input and the header). The active page has 3 screenshots, because I wanted to illustrate the other states that would be visible (in the table rows).

This is a moving/junk removal website, just for some context.

Here's some example websites (flat designs) that I like, just to give you an idea of what I'm after.

https://www.plimvora.com/
https://dacklow.com/
https://trevanu.com/
https://quobrintal.com/en/

Coding

Coded - Design and coding required

Number of Pages Required

5+ page

Colors

Designer to choose colors to be used in the design.

Requirements
Must have
• It must be a modern/simple flat design, that is built around the existing logo (attached).
• It has to be implemented using bootstrap.

```html
<!DOCTYPE html>
<html lang="en">
<head>
<meta charset="utf-8">
<title>Haulby – Booking Details</title>
<link href="https://fonts.googleapis.com/css2?family=Raleway:ital,wght@0,400;0,500;0,600;0,700;1,400&display=swap" rel="stylesheet">
<style>
:root{
  --brand:#4cc8f4;
  --brand-soft:#93e2fc;
  --accent:#ff8a00;
  --page:#ebebeb;
  --field:#f3f3f3;
  --ink:#333;
  --ink-strong:#222;
  --muted:#555;
  --ok:#1cb81c;
  --wait:#e03a10;
  --white:#fff;
  --rule:#cfcfcf;
  --row-alt:#f7f7f7;
}
*{box-sizing:border-box;margin:0;padding:0}
html,body{width:1200px;height:983px;overflow:hidden}
body{font-family:"Raleway",sans-serif;color:var(--ink);background:var(--white);position:relative}
.site-header{position:absolute;left:0;top:0;width:1200px;height:104px;background:var(--white)}
.brand{position:absolute;left:75px;top:30px;display:flex;align-items:center;gap:10px;color:var(--brand);font-weight:700;font-size:38px;letter-spacing:1px;white-space:nowrap}
.brand-dot{width:22px;height:22px;border-radius:50%;background:var(--brand)}
.main-nav{position:absolute;left:0;top:0;width:1200px;height:104px}
.main-nav a{position:absolute;top:0;height:104px;line-height:104px;font-size:13.5px;font-weight:600;color:var(--muted);text-decoration:none;letter-spacing:.3px;white-space:nowrap}
.nav-book{left:582px}
.nav-how{left:655px}
.nav-driver{left:774px;width:152px;text-align:center;background:var(--brand);color:var(--white)!important}
.account{position:absolute;left:962px;top:34px;width:166px;height:36px;background:var(--field);border-radius:2px;font-size:14px;color:var(--ink-strong);line-height:36px;padding-left:13px;white-space:nowrap}
.account svg{position:absolute;right:13px;top:15px}
.page{position:absolute;left:0;top:104px;width:1200px;height:804px;background:var(--page)}
.panel{position:absolute;left:75px;width:1051px;background:var(--white);border-radius:2px;overflow:hidden}
.panel-head{height:53px;background:var(--brand);color:var(--white);display:flex;align-items:center;padding-left:21px;gap:14px;font-size:21px;font-weight:600;letter-spacing:.4px}
.booking{top:43px;height:342px}
.field-label{position:absolute;font-size:13px;font-weight:700;color:var(--ink-strong);letter-spacing:.2px;white-space:nowrap}
.field{position:absolute;background:var(--field);border-radius:2px;font-size:14px;color:var(--ink);padding-left:22px}
.btn{position:absolute;background:var(--accent);color:var(--white);font-size:12.5px;font-weight:700;letter-spacing:.5px;text-align:center;border-radius:2px;white-space:nowrap}
.drivers{top:406px;height:356px}
.notice{height:54px;background:var(--brand-soft);font-style:italic;font-size:14.5px;color:var(--ink-strong);line-height:54px;padding-left:25px}
.table{width:100%;border-collapse:collapse;font-size:14px}
.table th{height:53px;text-align:left;font-size:13px;font-weight:700;color:var(--ink-strong);border-bottom:1px solid var(--rule);letter-spacing:.2px}
.table td{height:49px;white-space:nowrap}
.table tbody tr:first-child td{padding-top:10px}
.table tr.alt td{background:var(--row-alt)}
.c1{padding-left:25px;width:291px}.c2{width:199px}.c3{width:266px}
.status{font-weight:700;font-size:13.5px}
.accepted{color:var(--ok)}.sent{color:var(--brand)}.pending{color:var(--wait)}
.pay{position:absolute;left:981px;top:125px;width:119px;height:36px;line-height:36px}
.site-footer{position:absolute;left:0;top:908px;width:1200px;height:75px;text-align:center;font-size:12.5px;color:var(--muted);line-height:80px}
</style>
</head>
<body>
<header class="site-header">
  <div class="brand"><span class="brand-dot"></span>Haulby</div>
  <nav class="main-nav">
    <a class="nav-book" href="#">BOOK</a>
    <a class="nav-how" href="#">HOW IT WORKS</a>
    <a class="nav-driver" href="#">BECOME A DRIVER</a>
  </nav>
  <div class="account">mara@plendor.com
    <svg width="9" height="6" viewBox="0 0 9 6"><path d="M1 1l3.5 3.5L8 1" fill="none" stroke="#333" stroke-width="1.4"/></svg>
  </div>
</header>

<main class="page">
  <section class="panel booking">
    <div class="panel-head">
      <svg width="19" height="19" viewBox="0 0 19 19"><rect width="19" height="19" rx="3" fill="#fff"/><path d="M5 14l1-3 6-6 2 2-6 6z" fill="#4cc8f4"/></svg>
      BOOKING DETAILS
    </div>
    <div class="field-label" style="left:28px;top:78px">PACKAGE SELECTED</div>
    <div class="field" style="left:28px;top:101px;width:484px;height:46px;line-height:46px">Package 1
      <svg style="position:absolute;right:24px;top:17px" width="8" height="12" viewBox="0 0 8 12"><path d="M4 0l4 5H0zM4 12L0 7h8z" fill="#333"/></svg>
    </div>
    <div class="field-label" style="left:539px;top:78px">PICK UP TIME SELECTED</div>
    <div class="field" style="left:540px;top:101px;width:483px;height:46px;line-height:46px">July 18 at 14:31am
      <svg style="position:absolute;right:20px;top:16px" width="13" height="13" viewBox="0 0 13 13"><rect x=".5" y="2" width="12" height="10.5" fill="none" stroke="#444"/><rect x=".5" y="2" width="12" height="3" fill="#444"/><path d="M3 0v3M10 0v3" stroke="#444" stroke-width="1.5"/></svg>
    </div>
    <div class="field-label" style="left:28px;top:166px">DESCRIPTION</div>
    <div class="field" style="left:28px;top:189px;width:995px;height:85px;padding-top:16px">1 Large Stove</div>
    <div class="btn" style="left:28px;top:283px;width:117px;height:36px;line-height:36px">UPDATE</div>
  </section>

  <section class="panel drivers">
    <div class="panel-head">
      <svg width="24" height="20" viewBox="0 0 24 20"><path d="M4 8l2-6h12l2 6h2v8h-3v3h-3v-3H8v3H5v-3H2V8z" fill="#fff"/><rect x="7" y="4" width="10" height="4" fill="#4cc8f4"/><circle cx="6" cy="12" r="1.6" fill="#4cc8f4"/><circle cx="18" cy="12" r="1.6" fill="#4cc8f4"/></svg>
      DRIVERS IN YOUR AREA
    </div>
    <div class="notice">Please stay on this page and be patient, while we contact the drivers and find you on ASAP.</div>
    <table class="table">
      <thead><tr><th class="c1">NAME</th><th class="c2">DISTANCE</th><th class="c3">AGREED PICK UP TIME</th><th></th></tr></thead>
      <tbody>
        <tr><td class="c1">Dorian Vell</td><td>4.04km away</td><td>July18 at 14:13 am</td><td><span class="status accepted">Time Accepted</span></td></tr>
        <tr class="alt"><td class="c1">Perrin Hale</td><td>5.07km away</td><td>-</td><td><span class="status sent">Request Sent</span></td></tr>
        <tr><td class="c1">Osric Lane</td><td>11.13km away</td><td>-</td><td><span class="status sent">Request Sent</span></td></tr>
        <tr class="alt"><td class="c1">Tamsin Roe</td><td>11.19km away</td><td>-</td><td><span class="status pending">Pending</span></td></tr>
      </tbody>
    </table>
  </section>
  <span class="btn pay" style="top:570px">MAKE PAYMENT</span>
</main>

<footer class="site-footer">Copyright © 2017. Company Name. All Right Reserved</footer>
</body>
</html>
```